Upmarket Dessert Lounge needs a Business Card Design

We are an upmarket dessert lounge needing a business card to match our image.

We want something that is simple yet beautiful, feminine, classy, sophisticated and elegant. We want it to stand out and don't mind if it is bold.

The design should include our logo and colours of red or maroon with gold highlights. We don't mind if black is used.

Marlow & Quince

Target Market(s)

For those who like to indulge or treat themselves and give in to their temptations on good quality desserts.

Industry/Entity Type

Business

Requirements
Must have
• Must include our logo and our name

Marlow & Quince

M & Q

```html
<!DOCTYPE html>
<html lang="en">
<head>
<meta charset="utf-8">
<title>Marlow &amp; Quince — Business Card</title>
<link rel="stylesheet" href="https://fonts.googleapis.com/css2?family=Open+Sans:wght@400;600&display=swap">
<style>
  :root {
    --backdrop: #d9d6d2;
    --card-black: #1f1613;
    --gold: #e8b57a;
    --gold-deep: #c8904f;
    --maroon: #8a1f1c;
    --maroon-dark: #5e1311;
    --maroon-light: #a8302a;
    --ink-maroon: #7a2420;
    --paper: #ffffff;
    --paper-shade: #efeceb;
    --text-light: #f6ece6;
  }
  * { box-sizing: border-box; margin: 0; padding: 0; }
  html, body { width: 1200px; height: 951px; overflow: hidden; }
  body {
    background: var(--backdrop);
    font-family: "Open Sans", Verdana, sans-serif;
    position: relative;
  }
  .card {
    position: absolute;
    width: 640px;
    height: 372px;
    border-radius: 26px;
    overflow: hidden;
    box-shadow: 0 10px 26px rgba(0,0,0,.28);
  }
  /* Front */
  .card--front {
    left: 80px; top: 60px;
    background: radial-gradient(ellipse at 40% 40%, #2a1e1a 0%, var(--card-black) 70%);
  }
  .front__ornament {
    position: absolute;
    right: 30px; top: 0;
    width: 300px; height: 96px;
    border-radius: 0 0 40px 60px;
    background: linear-gradient(100deg, rgba(232,181,122,0) 0%, rgba(232,181,122,.55) 40%, rgba(232,181,122,.35) 100%);
  }
  .front__brand {
    position: absolute;
    left: 78px; top: 138px;
    width: 260px;
    text-align: center;
    font-size: 28px;
    font-weight: 600;
    letter-spacing: 1px;
    color: var(--gold);
  }
  .front__web {
    position: absolute;
    left: 150px; top: 286px;
    font-size: 16px;
    letter-spacing: 3px;
    color: var(--gold);
  }
  /* Back */
  .card--back {
    left: 480px; top: 500px;
    background: linear-gradient(180deg, var(--paper) 0%, var(--paper-shade) 50%);
  }
  .back__waves { position: absolute; inset: 0; width: 100%; height: 100%; }
  .back__brand-mark {
    position: absolute;
    left: 34px; top: 44px;
    font-size: 22px;
    font-weight: 600;
    color: var(--ink-maroon);
  }
  .back__name {
    position: absolute;
    right: 40px; top: 44px;
    font-size: 22px;
    color: var(--ink-maroon);
  }
  .back__address, .back__contacts {
    position: absolute;
    color: var(--text-light);
    font-size: 17px;
    line-height: 25px;
    list-style: none;
  }
  .back__address { left: 40px; top: 250px; padding-left: 26px; }
  .back__address .icon { position: absolute; left: 0; top: 4px; }
  .back__contacts { left: 370px; top: 250px; }
  .back__contacts li { display: flex; align-items: center; gap: 12px; }
  .icon { width: 14px; height: 14px; fill: var(--gold); flex: none; }
</style>
</head>
<body>
  <section class="card card--front">
    <div class="front__ornament" role="img" aria-label="Gold flourish ornament across the top corner"></div>
    <div class="front__brand">Marlow &amp; Quince</div>
    <div class="front__web">www.marlowquince.com</div>
  </section>

  <section class="card card--back">
    <svg class="back__waves" viewBox="0 0 640 372" preserveAspectRatio="none" aria-hidden="true">
      <defs>
        <radialGradient id="maroonFill" cx="40%" cy="70%" r="75%">
          <stop offset="0" stop-color="#a8302a"/>
          <stop offset="0.6" stop-color="#8a1f1c"/>
          <stop offset="1" stop-color="#5e1311"/>
        </radialGradient>
      </defs>
      <path d="M0 150 C160 120 320 190 470 150 S610 115 640 122 L640 372 L0 372 Z" fill="#1f1613"/>
      <path d="M0 164 C160 134 320 204 470 164 S610 129 640 136 L640 372 L0 372 Z" fill="#e8b57a"/>
      <path d="M0 170 C160 140 320 210 470 170 S610 135 640 142 L640 372 L0 372 Z" fill="url(#maroonFill)"/>
    </svg>

    <div class="back__brand-mark">Marlow &amp; Quince</div>
    <div class="back__name">Marlow &amp; Quince</div>

    <address class="back__address" style="font-style:normal">
      <svg class="icon" viewBox="0 0 14 14"><path d="M7 1 L13 7 H11 V13 H8.5 V9 H5.5 V13 H3 V7 H1 Z"/></svg>
      418 Linden Crest Rd.<br>Suite 204-118<br>Harlow, TX 78419
    </address>

    <ul class="back__contacts">
      <li><svg class="icon" viewBox="0 0 14 14"><path d="M3 1 L5.5 1 L6.5 4.5 L5 5.7 C5.8 7.6 6.6 8.4 8.3 9 L9.5 7.5 L13 8.5 L13 11 C13 12 12 13 11 13 C5.5 12.5 1.5 8.5 1 3 C1 2 2 1 3 1 Z"/></svg>555-014-2730</li>
      <li><svg class="icon" viewBox="0 0 14 14"><path d="M3 1 H10 V5 H3 Z M1 6 H13 V12 H1 Z M4 9 H10 V13 H4 Z"/></svg>555-014-2731</li>
      <li><svg class="icon" viewBox="0 0 14 14"><path d="M1 3 H13 V11 H1 Z M1.5 3.5 L7 8 L12.5 3.5" stroke="#8a1f1c" stroke-width="1"/></svg>info@marlowquince.com</li>
      <li><svg class="icon" viewBox="0 0 14 14"><circle cx="7" cy="7" r="6"/></svg>www.marlowquince.com</li>
    </ul>
  </section>
</body>
</html>
```